Harborline Renewal Business Card Design

Professional and clean design. The design colors should flow with the logo. Two-sided card with the website on the back which is:

www.HarborlineRenewal.example.

"Specializing in Water Damage Restoration"

On the front I need the name, email, phone, and logo.

Name: Darnell Quisby
Email: Darnell@HarborlineRenewal.example
Phone: 555-318-2046 for now

I only have the Preview and Thumbnail right now but should have the source files uploaded within a day or two.

Target Market(s)

Flood victims, home owners with water damage from busted pipes etc...

Industry/Entity Type

Business

Contact Information for Business Card

Name: Darnell Quisby

Font styles to use
Serif
Sans Serif

Requirements
Must have
• Business Card Details Info

```html
<!DOCTYPE html>
<html lang="en">
<head>
<meta charset="utf-8">
<title>Harborline Renewal Business Card</title>
<link href="https://fonts.googleapis.com/css2?family=Open+Sans:wght@400;600;700&display=swap" rel="stylesheet">
<style>
  :root {
    --brand-blue: #2a98d6;
    --brand-blue-light: #5bbbe8;
    --paper: #ffffff;
    --backdrop: #2b2b2b;
    --ink-soft: #e8f4fb;
  }
  * { box-sizing: border-box; margin: 0; padding: 0; }
  html, body { width: 1200px; height: 900px; overflow: hidden; }
  body {
    background: var(--backdrop);
    font-family: "Open Sans", Arial, sans-serif;
    position: relative;
  }
  .card {
    position: absolute;
    width: 560px;
    height: 320px;
    border-radius: 22px;
    overflow: hidden;
  }

  /* Back side */
  .card-back {
    left: 60px; top: 80px;
    background: var(--brand-blue);
    color: var(--paper);
    text-align: center;
  }
  .back-mark {
    position: absolute;
    left: 50%; top: 38px;
    transform: translateX(-50%);
    display: flex; align-items: center; gap: 14px;
  }
  .back-mark .mark-circle {
    width: 120px; height: 120px; border-radius: 50%;
    background: var(--paper);
  }
  .back-mark .mark-name {
    font-weight: 600; font-size: 26px; color: var(--paper);
    text-align: left; line-height: 1.15; width: 150px;
  }
  .back-tagline {
    position: absolute; left: 0; right: 0; top: 214px;
    font-size: 14.5px; letter-spacing: 0.3px; text-transform: uppercase;
  }
  .back-website {
    position: absolute; left: 0; right: 0; top: 244px;
    font-size: 16px;
  }

  /* Front side */
  .card-front {
    left: 580px; top: 500px;
    background: var(--paper);
    color: var(--brand-blue);
  }
  .front-mark {
    position: absolute; left: 34px; top: 34px;
    display: flex; align-items: center; gap: 12px;
  }
  .front-mark .mark-circle {
    width: 58px; height: 58px; border-radius: 50%;
    background: var(--brand-blue);
  }
  .front-mark .mark-name {
    font-weight: 600; font-size: 24px; color: var(--brand-blue);
  }
  .holder-name {
    position: absolute; right: 48px; top: 122px;
    font-weight: 700; font-size: 24px; text-transform: uppercase;
    letter-spacing: 0.4px;
  }
  .name-rule {
    position: absolute; left: 250px; right: 30px; top: 158px;
    height: 2px; background: var(--brand-blue);
  }
  .name-dot {
    position: absolute; right: -14px; top: 146px;
    width: 28px; height: 28px; border-radius: 50%;
    border: 3px solid var(--brand-blue-light); background: var(--paper);
  }
  .contact-rule {
    position: absolute; left: 30px; width: 250px; top: 196px;
    height: 1.5px; background: var(--brand-blue);
  }
  .contact-list {
    position: absolute; left: 32px; top: 204px;
    list-style: none; font-size: 15px; line-height: 22px;
  }
  .contact-list li { display: flex; align-items: center; gap: 8px; }
  .contact-list svg { width: 13px; height: 13px; flex: none; }
  .front-band {
    position: absolute; left: 0; right: 0; bottom: 0; height: 36px;
    background: var(--brand-blue);
  }
  .band-dot {
    position: absolute; left: 50%; top: -12px; transform: translateX(-50%);
    width: 30px; height: 30px; border-radius: 50%;
    background: var(--paper); border: 3px solid var(--brand-blue);
  }
</style>
</head>
<body>

  <section class="card card-back" aria-label="Card back">
    <div class="back-mark">
      <span class="mark-circle"></span>
      <span class="mark-name">Harborline Renewal</span>
    </div>
    <p class="back-tagline">Specializing in Water Damage Restoration</p>
    <p class="back-website">www.HarborlineRenewal.example</p>
  </section>

  <section class="card card-front" aria-label="Card front">
    <div class="front-mark">
      <span class="mark-circle"></span>
      <span class="mark-name">Harborline Renewal</span>
    </div>
    <h1 class="holder-name">Darnell Quisby</h1>
    <div class="name-rule"></div>
    <span class="name-dot"></span>
    <div class="contact-rule"></div>
    <ul class="contact-list">
      <li>
        <svg viewBox="0 0 24 24" aria-hidden="true"><path fill="#2a98d6" d="M6.6 10.8a15.1 15.1 0 0 0 6.6 6.6l2.2-2.2c.3-.3.7-.4 1-.2 1.1.4 2.3.6 3.6.6.6 0 1 .4 1 1V20c0 .6-.4 1-1 1A17 17 0 0 1 3 4c0-.6.4-1 1-1h3.5c.6 0 1 .4 1 1 0 1.3.2 2.5.6 3.6.1.3 0 .7-.2 1z"/></svg>
        555-318-2046
      </li>
      <li>
        <svg viewBox="0 0 24 24" aria-hidden="true"><rect x="2" y="5" width="20" height="14" rx="2" fill="none" stroke="#2a98d6" stroke-width="2"/><path d="M3 6l9 7 9-7" fill="none" stroke="#2a98d6" stroke-width="2"/></svg>
        Darnell@HarborlineRenewal.example
      </li>
      <li>
        <svg viewBox="0 0 24 24" aria-hidden="true"><circle cx="12" cy="12" r="9" fill="none" stroke="#2a98d6" stroke-width="2"/><path d="M3 12h18M12 3c3 3 3 15 0 18M12 3c-3 3-3 15 0 18" fill="none" stroke="#2a98d6" stroke-width="1.6"/></svg>
        www.HarborlineRenewal.example
      </li>
    </ul>
    <div class="front-band"><span class="band-dot"></span></div>
  </section>

</body>
</html>
```